Audio-Visual & Video Communications Business Requires a Cutting-edge Business Card Design

LinkVerra is a new Audio-Visual & Video Communications company in Cape Town, South Africa that is looking for a cutting-edge business card design. We sell these products to the Corporate, Education & Hospitality markets and will also host an Online Shop for companies and individuals to purchase our products online.

We are already using the following two colours in our logo and draft website. Please incorporate these colours into the design. Please note that our website is still in the design stage if you need to visit it. Green #a0ce4e & Dark Grey #333333.

Hi,

Please note that I have uploaded our logo in an .eps format.

Target Market(s)

Corporate Companies, Education Institutions & Hospitality Markets

Industry/Entity Type

Business

Requirements
Nice to have
• It would be great if you could incorporate the services that we offer.

1. Consultation & Design
2. Project Management
3. Supply & Installation
4. Onsite Support Personal
5. Online Shop

```html
<!DOCTYPE html>
<html lang="en">
<head>
<meta charset="utf-8">
<title>LinkVerra Business Card</title>
<link rel="stylesheet" href="https://fonts.googleapis.com/css2?family=Arimo:wght@400;700&family=Open+Sans:wght@600;700&display=swap">
<style>
  :root {
    --green: #79bb1a;
    --charcoal: #4a4a4a;
    --ink: #333333;
    --white: #ffffff;
    --muted: #c4c4c4;
    --page: #ffffff;
  }
  * { margin: 0; padding: 0; box-sizing: border-box; }
  html, body { width: 1200px; height: 900px; overflow: hidden; background: var(--page); }
  .canvas { position: relative; width: 1200px; height: 900px; font-family: "Arimo", Arial, sans-serif; }

  .card {
    position: absolute; left: 388px; width: 469px; height: 287px;
    border-radius: 18px; overflow: hidden; background: var(--charcoal);
    box-shadow: 0 14px 28px rgba(0,0,0,0.18);
  }
  .card--front { top: 115px; }
  .card--back { top: 488px; height: 286px; }
  .card__shapes { position: absolute; inset: 0; }

  .abs { position: absolute; white-space: nowrap; }

  .holder-name { left: 23px; top: 22px; font-size: 21px; color: var(--green); }
  .address { left: 22px; top: 52px; font-size: 13.5px; color: var(--white); }
  .phones { left: 23px; top: 71px; font-size: 13.5px; color: var(--white); display: flex; align-items: center; gap: 4px; }
  .phones svg { display: block; }
  .phones .gap { width: 12px; }

  .email { left: 290px; top: 146px; font-size: 13.5px; color: var(--green); }
  .email-rule { left: 290px; top: 166px; width: 179px; height: 3px; background: var(--green); }

  .brand { display: flex; flex-direction: column; align-items: center; }
  .brand__dot { width: 40px; height: 40px; border-radius: 50%; background: var(--green); margin-bottom: 14px; }
  .brand__name { font-family: "Open Sans", Arial, sans-serif; font-weight: 700; font-size: 25px; color: var(--green); letter-spacing: -0.2px; }
  .card--front .brand { left: 27px; top: 128px; width: 200px; }
  .card--back .brand { left: 214px; top: 128px; width: 200px; }

  .website { font-size: 16px; color: var(--ink); }
  .card--front .website { left: 28px; top: 257px; }
  .card--back .website { left: 218px; top: 256px; }

  .services { left: 24px; top: 93px; list-style: none; font-family: "Open Sans", Arial, sans-serif; font-weight: 700; font-size: 11.5px; line-height: 17px; color: var(--muted); }
</style>
</head>
<body>
<main class="canvas">

  <section class="card card--front" aria-label="Business card front">
    <svg class="card__shapes" width="469" height="287" viewBox="0 0 469 287" aria-hidden="true">
      <circle cx="127" cy="232" r="127" fill="var(--white)"/>
    </svg>
    <p class="abs holder-name">Daniel Mokoena</p>
    <p class="abs address">42 Harbour Lane • Cape Town - South Africa</p>
    <p class="abs phones">
      <svg width="9" height="13" viewBox="0 0 9 13" aria-hidden="true"><rect x="0.7" y="0.7" width="7.6" height="11.6" rx="1.2" fill="none" stroke="#fff" stroke-width="1.2"/><rect x="2" y="2.2" width="5" height="4" fill="#fff"/></svg>
      <span>+27 82 555-0134</span>
      <span class="gap"></span>
      <svg width="16" height="11" viewBox="0 0 16 11" aria-hidden="true"><path d="M1 4 Q8 -1 15 4 L13 5.5 L11 4 L5 4 L3 5.5 Z" fill="#fff"/><rect x="3" y="5" width="10" height="6" rx="1.5" fill="#fff"/></svg>
      <span>+27 21 555-0178</span>
    </p>
    <p class="abs email">me@linkverra.co.za</p>
    <div class="abs email-rule"></div>
    <div class="abs brand">
      <span class="brand__dot"></span>
      <span class="brand__name">LinkVerra</span>
    </div>
    <p class="abs website">www.linkverra.co.za</p>
  </section>

  <section class="card card--back" aria-label="Business card back">
    <svg class="card__shapes" width="469" height="286" viewBox="0 0 469 286" aria-hidden="true">
      <polygon points="374,0 469,0 469,286 260,286" fill="var(--green)"/>
      <circle cx="313" cy="212" r="130" fill="var(--white)"/>
    </svg>
    <ul class="abs services">
      <li>Consultation &amp; Design</li>
      <li>Project Management</li>
      <li>Supply &amp; Installation</li>
      <li>Onsite Support Personal</li>
      <li>Online Shop</li>
    </ul>
    <div class="abs brand">
      <span class="brand__dot"></span>
      <span class="brand__name">LinkVerra</span>
    </div>
    <p class="abs website">www.linkverra.co.za</p>
  </section>

</main>
</body>
</html>
```